Veranix - Solution provider in business consulting

Veranix is a swiss based company providing solutions for developing markets. The business covers various fields of business consulting, such as supply chain, product costs, quality management and manufacturing management. The Business operates in a efficient, straight and solution oriented manner.
The final design should communicate these characteristics. Asian people as well as as western people shall identify the qualities of the company at first sight.
The customer needs business cards with a simple view but an recognizable design, printed in high quality. Engraved elements such as the globe or simple words are possible.
Available colors are: (RAL)
102/102/102
51/102/102
153/204/153
255/102/51
Font: Calibri

```html
<!DOCTYPE html>
<html lang="en">
<head>
<meta charset="utf-8">
<title>Veranix – Business Card</title>
<link rel="stylesheet" href="https://fonts.googleapis.com/css2?family=Carlito:wght@400;700&display=swap">
<style>
  :root {
    --stage: #e4e4e2;
    --ink: #4d4d4d;
    --ink-soft: #8a8a8a;
    --card-white: #ffffff;
    --card-fade: #e2e2e2;
    --grey-dark: #3f3f3f;
    --grey-mid: #666666;
    --grey-light: #8c8c8c;
    --engrave: #c9c9c9;
    --engrave-soft: #a9a9a9;
  }
  * { box-sizing: border-box; margin: 0; padding: 0; }
  html, body {
    width: 1200px; height: 950px; overflow: hidden;
    background: var(--stage);
    font-family: "Carlito", "Calibri", Arial, sans-serif;
  }
  .canvas {
    width: 1200px; height: 950px;
    display: flex; flex-direction: column; align-items: center; justify-content: center;
    gap: 40px;
  }
  .card {
    position: relative; width: 700px; height: 420px; overflow: hidden;
    box-shadow: 0 6px 18px rgba(0,0,0,.18);
  }

  /* Front side */
  .card-front {
    background: linear-gradient(100deg, var(--card-white) 0%, var(--card-white) 50%, var(--card-fade) 100%);
  }
  .front-globe {
    position: absolute; left: 300px; top: 130px; width: 520px; height: 520px;
  }
  .brand {
    position: absolute; left: 42px; top: 36px;
    display: flex; align-items: center; gap: 12px;
  }
  .brand-dot { width: 30px; height: 30px; border-radius: 50%; background: var(--grey-mid); }
  .brand-name { font-size: 48px; font-weight: 400; color: var(--grey-mid); letter-spacing: 1px; line-height: 1; }

  .contact { position: absolute; left: 42px; top: 118px; color: var(--ink); }
  .contact-name { font-size: 26px; font-weight: 700; line-height: 1.1; }
  .contact-role { font-size: 15px; color: var(--ink-soft); margin-bottom: 14px; }
  .company { font-size: 18px; font-weight: 700; line-height: 1.25; }
  .address { font-size: 18px; line-height: 1.25; }
  .lines { list-style: none; margin-top: 4px; }
  .lines li { display: flex; align-items: center; gap: 8px; font-size: 18px; line-height: 1.3; }
  .lines svg { width: 16px; height: 16px; fill: var(--ink); flex: none; }

  /* Back side */
  .card-back {
    background: linear-gradient(95deg, var(--grey-dark) 0%, var(--grey-mid) 55%, var(--grey-light) 100%);
  }
  .back-brand {
    position: absolute; left: 0; right: 0; top: 150px;
    display: flex; align-items: center; justify-content: center; gap: 14px;
  }
  .back-brand .brand-name { color: var(--engrave); font-size: 56px; }
  .back-brand .brand-dot { width: 34px; height: 34px; background: var(--engrave); }
  .back-web {
    position: absolute; left: 0; right: 0; top: 246px; text-align: center;
    font-size: 20px; letter-spacing: 3px; color: var(--engrave-soft);
  }
</style>
</head>
<body>
<main class="canvas">

  <section class="card card-front" aria-label="Business card front">
    <svg class="front-globe" viewBox="0 0 520 520" role="img" aria-label="Globe with map of East Asia">
      <defs>
        <radialGradient id="frontGlobeFill" cx="0.55" cy="0.4" r="0.65">
          <stop offset="0" stop-color="#9a9a9a"/>
          <stop offset="1" stop-color="#5e5e5e"/>
        </radialGradient>
      </defs>
      <circle cx="260" cy="260" r="260" fill="url(#frontGlobeFill)"/>
    </svg>

    <div class="brand">
      <span class="brand-name">veranix</span>
      <span class="brand-dot"></span>
    </div>

    <div class="contact">
      <p class="contact-name">Lena Moser</p>
      <p class="contact-role">CEO</p>
      <p class="company">Veranix GmbH</p>
      <p class="address">Talgasse 18, 9230 Flawil</p>
      <p class="address">Switzerland</p>
      <ul class="lines">
        <li>
          <svg viewBox="0 0 16 16" aria-hidden="true"><path d="M2 5c0-2 2-3 6-3s6 1 6 3v1h-3V5H5v1H2zM4 7h8l2 7H2z"/></svg>
          +41 71 380 5172
        </li>
        <li>
          <svg viewBox="0 0 16 16" aria-hidden="true"><path d="M4 1h8v14H4zM5.5 3v9h5V3zM7 13h2v1H7z" fill-rule="evenodd"/></svg>
          +41 79 624 3809
        </li>
        <li>
          <svg viewBox="0 0 16 16" aria-hidden="true"><path d="M1 3h14v10H1zM2 4l6 5 6-5z" fill-rule="evenodd"/></svg>
          lena.moser@veranix.ch
        </li>
        <li>
          <svg viewBox="0 0 16 16" aria-hidden="true"><circle cx="8" cy="8" r="7"/></svg>
          www.veranix.ch
        </li>
      </ul>
    </div>
  </section>

  <section class="card card-back" aria-label="Business card back">
    <div class="back-brand">
      <span class="brand-name">veranix</span>
      <span class="brand-dot"></span>
    </div>
    <p class="back-web">www.veranix.ch</p>
  </section>

</main>
</body>
</html>
```